Celvara Health Group Presentation Folder, for Cancer Awareness, VERY COLORFUL AND MODERN

Presentation Folder I know pretty much what i want so it should be very eazy , I have included files from folders I use now rebrand them to my new company they will be fine, no sense re creating the wheel
Full Bleed Size
20.87" x 16.68"
53 x 42.4 cm
6260 x 5004 pixels
Document Trim Size
20.75" x 16.56"
52.7 x 42.1 cm
6225 x 4969 pixels

Low design quality

Industry/Entity Type

Medical

Font styles to use
Serif

Colors

Designer to choose colors to be used in the design.

Requirements
Must have
• really I am not looking for some one to redesign, we like our folder front page and would like to see new word information added., there are two folder front pages to choose from
• So Keep the original front page and redesign the back page and the pockets
• Can Make your Design off of one of the ones I already uploaded
Nice to have
• Keep the same color schemes, Keep the original front page and redesign the back page and the pockets
Should not have
• DO not recreate the front covers, use what I gave you and just rebrand

```html
<!DOCTYPE html>
<html lang="en">
<head>
<meta charset="utf-8">
<title>Celvara Health Group – Presentation Folder</title>
<link href="https://fonts.googleapis.com/css2?family=Raleway:wght@300;400;500;600;700&display=swap" rel="stylesheet">
<style>
  :root{
    --stage:#2e2e30;
    --paper:#ffffff;
    --green:#96c15f;
    --pink:#ec6f8f;
    --rose:#e77b8d;
    --navy:#1f2f5c;
    --grey-bar:#7a7a7c;
    --grey-edge:#d4d6d8;
    --guide:#9fd6ea;
    --body-text:#3a3a48;
    --ribbon-purple:#a766b0;
    --ribbon-pink:#e8a6c4;
    --ribbon-blue:#7cc9ec;
  }
  *{box-sizing:border-box;margin:0;padding:0}
  html,body{width:1200px;height:960px;overflow:hidden}
  body{background:var(--stage);font-family:"Raleway",Arial,sans-serif;position:relative}

  /* ---------- folder spread ---------- */
  .folder{position:absolute;width:642px;height:372px}
  .folder--inside{left:44px;top:69px}
  .folder--filled{left:44px;top:500px}
  .folder__flap{position:absolute;top:0;width:33px;height:100%;background:var(--green)}
  .folder__flap--left{left:0}
  .folder__flap--right{right:0}
  .folder__notch{position:absolute;top:222px;width:14px;height:14px;border-radius:50%;background:var(--paper)}
  .folder__notch--left{left:-7px}
  .folder__notch--right{right:-7px}
  .folder__page{position:absolute;top:0;height:100%;background:var(--paper);overflow:hidden}
  .folder__page--left{left:33px;width:286px;box-shadow:inset -14px 0 18px -12px rgba(0,0,0,.25)}
  .folder__page--right{left:319px;width:291px}
  .folder__guide{position:absolute;inset:6px 8px;border:1px solid var(--guide);pointer-events:none}
  .folder__insert{position:absolute;left:0;top:0;width:294px;height:372px;transform-origin:0 0}
  .folder__page--left .folder__insert{transform:scale(.97)}
  .folder__page--right .folder__insert{transform:scale(.99)}

  .pocket{position:absolute;top:229px;height:143px}
  .pocket--left{left:33px;width:286px}
  .pocket--right{left:319px;width:291px}
  .pocket svg{position:absolute;inset:0}
  .pocket__brand{position:absolute;left:36px;bottom:18px;color:var(--pink);font-size:11px;font-weight:500;letter-spacing:.2px;line-height:1.1}
  .pocket__brand small{display:block;font-size:7.5px;color:var(--pink);font-weight:400;letter-spacing:0}
  .pocket__logo{position:absolute;right:22px;bottom:26px;display:flex;align-items:center;gap:8px}
  .pocket__logo-dot{width:36px;height:36px;border-radius:50%;background:var(--navy)}
  .pocket__logo-name{font-size:15px;font-weight:700;line-height:1.02;color:var(--navy);letter-spacing:.3px;text-transform:uppercase}

  /* ---------- loose sheets ---------- */
  .sheet{position:absolute;width:294px;height:370px;background:var(--paper);overflow:hidden}
  .sheet--back{left:782px;top:69px}
  .sheet--front{left:791px;top:500px}

  .info__copy{position:absolute;left:11px;top:9px;width:225px;font-size:5.6px;line-height:1.38;color:var(--body-text);text-align:justify}
  .info__copy p+p{margin-top:5px}
  .info__ribbon{position:absolute;right:6px;top:0;width:78px;height:230px;border-radius:0 0 6px 6px;
    background:linear-gradient(180deg,var(--ribbon-purple) 0%,var(--ribbon-pink) 50%,var(--ribbon-blue) 100%);opacity:.85}
  .info__band{position:absolute;left:0;top:128px;width:250px;height:38px;padding:6px 12px;
    background:linear-gradient(90deg,var(--rose),#f3b3bf);color:#fff;font-size:9.6px;font-weight:700;line-height:1.25}
  .info__photo{position:absolute;left:0;top:166px;width:100%;height:204px;
    background:linear-gradient(180deg,#8fcdf0 0%,#cde9f7 45%,#e9efee 62%,#d9c8a8 100%)}

  .cover__title{position:absolute;left:0;width:100%;top:48px;text-align:center;color:var(--pink);font-size:16.5px;font-weight:400;letter-spacing:.2px}
  .cover__tag{position:absolute;left:25px;width:244px;top:73px;height:15px;background:var(--grey-bar);color:#fff;font-size:7.6px;text-align:center;line-height:15px;letter-spacing:.1px}
  .cover__lede{position:absolute;left:30px;width:234px;top:93px;text-align:center;color:var(--navy);font-size:5.8px;line-height:1.4;text-transform:uppercase}
  .cover__ribbons{position:absolute;left:16px;width:262px;top:150px;height:110px;border-radius:6px;
    background:linear-gradient(90deg,#f3bfd0 0%,#e9a3c6 35%,#c9a6d6 50%,#e9a3c6 65%,#f3bfd0 100%)}
  .cover__footer{position:absolute;left:0;width:100%;top:318px;height:26px;background:var(--grey-bar);display:flex;align-items:center;padding-left:20px;gap:12px;color:#fff;font-size:10px;font-weight:500}
  .cover__footer-dot{width:22px;height:22px;border-radius:50%;background:var(--paper)}
</style>
</head>
<body>

<!-- Inside spread, empty -->
<div class="folder folder--inside">
  <div class="folder__flap folder__flap--left"><span class="folder__notch folder__notch--left"></span></div>
  <div class="folder__flap folder__flap--right"><span class="folder__notch folder__notch--right"></span></div>
  <div class="folder__page folder__page--left"><div class="folder__guide"></div></div>
  <div class="folder__page folder__page--right"><div class="folder__guide"></div></div>

  <div class="pocket pocket--left">
    <svg width="286" height="143" viewBox="0 0 286 143">
      <rect width="286" height="143" fill="var(--green)"/>
      <path d="M0 18 Q0 4 14 4 H150 Q235 20 268 143 H0 Z" fill="var(--paper)"/>
      <rect x="0" y="4" width="12" height="139" fill="var(--grey-edge)"/>
      <path d="M45 25 Q150 25 150 105" fill="none" stroke="#d6d6d6" stroke-width="1"/>
      <g stroke="#bdbdbd" stroke-width="1">
        <line x1="55" y1="35" x2="65" y2="45"/><line x1="135" y1="35" x2="125" y2="45"/>
        <line x1="55" y1="95" x2="65" y2="85"/><line x1="135" y1="95" x2="125" y2="85"/>
      </g>
    </svg>
    <div class="pocket__brand">CELVARA HEALTH GROUP<small>a division of Meridian Clinical Sales LLC</small></div>
  </div>
  <div class="pocket pocket--right">
    <svg width="291" height="143" viewBox="0 0 291 143">
      <rect width="291" height="143" fill="var(--paper)"/>
      <path d="M0 4 H75 Q30 25 22 143 H0 Z" fill="var(--green)"/>
      <rect x="270" y="30" width="12" height="113" fill="var(--grey-edge)"/>
    </svg>
    <div class="pocket__logo"><span class="pocket__logo-dot"></span><span class="pocket__logo-name">Celvara<br>Health<br>Group</span></div>
  </div>
</div>

<!-- Back sheet -->
<div class="sheet sheet--back">
  <div class="info__copy">
    <p>There are many benefits to getting tested, regardless of the eventual result. If one of your family members — however distant — had cancer, there is a chance that you inherited a gene mutation that not only increases your personal risk of cancer, but also could be passed to the next generation. Those who are carriers of hereditary cancer gene mutations, could be at risk of getting cancer earlier in life than the general population. The sooner genetic testing is done, the more likely it is that the risk can be managed appropriately.</p>
    <p>Hereditary cancer screening provides vital information to help people with a strong personal or family history of cancer understand their own risk of developing the disease. With this information, they can take steps to Potentially Prevent Cancer, Delay the Onset of Cancer or Catch it at an Earlier stage when outcomes and survival rates are Better.</p>
  </div>
  <div class="info__ribbon" role="img" aria-label="Illustration of a large awareness ribbon in purple, pink and blue"></div>
  <div class="info__band">Identifying an inherited genetic mutation has the potential to prevent cancer and save lives.</div>
  <div class="info__photo" role="img" aria-label="Photo of a multi-generation family walking hand in hand on a sunny beach"></div>
</div>

<!-- Filled spread -->
<div class="folder folder--filled">
  <div class="folder__flap folder__flap--left"><span class="folder__notch folder__notch--left"></span></div>
  <div class="folder__flap folder__flap--right"><span class="folder__notch folder__notch--right"></span></div>
  <div class="folder__page folder__page--left">
    <div class="folder__insert">
      <div class="info__copy">
        <p>There are many benefits to getting tested, regardless of the eventual result. If one of your family members — however distant — had cancer, there is a chance that you inherited a gene mutation that not only increases your personal risk of cancer, but also could be passed to the next generation. Those who are carriers of hereditary cancer gene mutations, could be at risk of getting cancer earlier in life than the general population. The sooner genetic testing is done, the more likely it is that the risk can be managed appropriately.</p>
        <p>Hereditary cancer screening provides vital information to help people with a strong personal or family history of cancer understand their own risk of developing the disease. With this information, they can take steps to Potentially Prevent Cancer, Delay the Onset of Cancer or Catch it at an Earlier stage when outcomes and survival rates are Better.</p>
      </div>
      <div class="info__ribbon" role="img" aria-label="Illustration of a large awareness ribbon in purple, pink and blue"></div>
      <div class="info__band">Identifying an inherited genetic mutation has the potential to prevent cancer and save lives.</div>
      <div class="info__photo" role="img" aria-label="Photo of a family walking on a beach"></div>
    </div>
    <div class="folder__guide"></div>
  </div>
  <div class="folder__page folder__page--right">
    <div class="folder__insert">
      <div class="cover__title">HEREDITARY CANCER SCREENING</div>
      <div class="cover__tag">DOCTORS ARE THE GATEKEEPERS TO GENETIC TESTING.</div>
      <div class="cover__lede">We have an obligation to help patients understand genetic<br>risk and how testing can guide heath care decisions.</div>
      <div class="cover__ribbons" role="img" aria-label="Illustration of a row of pink awareness ribbons around a central purple and blue ribbon"></div>
    </div>
    <div class="folder__guide"></div>
  </div>

  <div class="pocket pocket--left">
    <svg width="286" height="143" viewBox="0 0 286 143">
      <rect width="286" height="143" fill="var(--green)"/>
      <path d="M0 18 Q0 4 14 4 H150 Q235 20 268 143 H0 Z" fill="var(--paper)"/>
      <path d="M45 25 Q150 25 150 105" fill="none" stroke="#d6d6d6" stroke-width="1"/>
      <g stroke="#bdbdbd" stroke-width="1">
        <line x1="55" y1="35" x2="65" y2="45"/><line x1="135" y1="35" x2="125" y2="45"/>
        <line x1="55" y1="95" x2="65" y2="85"/><line x1="135" y1="95" x2="125" y2="85"/>
      </g>
    </svg>
    <div class="pocket__brand">CELVARA HEALTH GROUP<small>a division of Meridian Clinical Sales LLC</small></div>
  </div>
  <div class="pocket pocket--right">
    <svg width="291" height="143" viewBox="0 0 291 143">
      <rect width="291" height="143" fill="var(--paper)"/>
      <path d="M0 4 H75 Q30 25 22 143 H0 Z" fill="var(--green)"/>
      <rect x="270" y="30" width="12" height="113" fill="var(--grey-edge)"/>
    </svg>
    <div class="pocket__logo"><span class="pocket__logo-dot"></span><span class="pocket__logo-name">Celvara<br>Health<br>Group</span></div>
  </div>
</div>

<!-- Front cover sheet -->
<div class="sheet sheet--front">
  <div class="cover__title">HEREDITARY CANCER SCREENING</div>
  <div class="cover__tag">DOCTORS ARE THE GATEKEEPERS TO GENETIC TESTING.</div>
  <div class="cover__lede">We have an obligation to help patients understand genetic<br>risk and how testing can guide heath care decisions.</div>
  <div class="cover__ribbons" role="img" aria-label="Illustration of a row of pink awareness ribbons around a central purple and blue ribbon, each labelled with a cancer type"></div>
  <div class="cover__footer"><span class="cover__footer-dot"></span>The test you order FOR your patients</div>
</div>

</body>
</html>
```